Marcus Delbridge Finance

Need a personal website advertising Equipment Finance,Business Finance,Commercial Finance, Construction Finance, Bridging Finance. Similar websites are www.corvalend.com.au / www.tarmivest.com.au / www.qbr7.com.au /wwwhalvecredit.com.au

Target Market(s)

Business People

Industry/Entity Type

Business

Number of Pages Required

3 page

Font styles to use
Serif
Sans Serif

Requirements
Must have
• All i want is a simple corporate looking website advertising Equipment Finance, Commercial Finance, Construction Finance, Business Finance, Bridging Finance,

```html
<!DOCTYPE html>
<html lang="en">
<head>
<meta charset="utf-8">
<title>Marcus Delbridge Finance</title>
<link rel="stylesheet" href="https://fonts.googleapis.com/css2?family=Open+Sans:wght@400;600;700&family=Roboto:wght@300;400;500;700&display=swap">
<style>
:root{
  --navy:#0d3a66;
  --navy-deep:#0b2a4d;
  --sky:#00a9e8;
  --ice:#eef5fc;
  --line:#e3e9ef;
  --grey-text:#8a8f95;
  --body-text:#3b3f44;
  --footer:#e3e7ea;
  --white:#ffffff;
}
*{box-sizing:border-box;margin:0;padding:0}
html,body{width:690px;height:1200px;overflow:hidden;background:var(--white)}
body{font-family:"Open Sans",Arial,sans-serif;color:var(--body-text);position:relative}
a{color:inherit;text-decoration:none}
.wrap{position:absolute;left:88px;width:517px}

/* top bar */
.topbar{position:absolute;top:0;left:0;width:690px;height:22px;background:#f4f8fc;border-bottom:1px solid var(--line)}
.topbar .contact{position:absolute;left:92px;top:0;height:22px;line-height:22px;font-size:6.5px;color:var(--navy);padding:0 7px;border-left:1px solid var(--line);border-right:1px solid var(--line)}
.topbar .socials{position:absolute;left:139px;top:5px;display:flex;gap:9px}
.topbar .socials span{width:11px;height:11px;border-radius:50%;background:var(--navy);display:block}
.quote-tab{position:absolute;left:535px;top:4px;width:68px;height:18px;background:var(--navy-deep);color:var(--white);font-size:6.5px;line-height:18px;text-align:center;border-radius:3px 3px 0 0}

/* header */
.header{position:absolute;top:22px;left:0;width:690px;height:45px;background:var(--white)}
.logo{position:absolute;left:88px;top:10px;font-family:"Roboto",sans-serif;font-weight:700;color:var(--navy);font-size:12px;line-height:13px;width:100px}
.mainnav{position:absolute;left:192px;top:18px;display:flex;gap:14px;font-size:6.5px;color:var(--navy)}
.mainnav .active{border-bottom:2px solid var(--sky);padding-bottom:3px}
.phone{position:absolute;right:87px;top:12px;font-family:"Roboto",sans-serif;font-size:14px;color:var(--navy)}

/* service nav */
.servicenav{position:absolute;top:67px;left:0;width:690px;height:21px;background:var(--sky);display:flex;gap:0;padding-left:88px;align-items:center}
.servicenav a{color:var(--white);font-size:7.5px;margin-right:17px}

/* hero */
.hero{position:absolute;top:88px;left:0;width:690px;height:216px;background:linear-gradient(90deg,#d6e4ef 0%,#eaf1f6 45%,#dde7ef 70%,#c3cfd9 100%)}
.hero-photo{position:absolute;right:0;top:0;width:200px;height:216px;background:linear-gradient(180deg,#d8cfc7 0%,#3c4550 45%,#1d232b 100%)}
.hero-text{position:absolute;left:93px;top:53px}
.hero h1{font-family:"Roboto",sans-serif;font-weight:700;font-size:19.5px;color:var(--navy);letter-spacing:.2px}
.hero p{font-family:"Roboto",sans-serif;font-size:12px;line-height:15px;color:var(--navy);margin-top:4px;width:300px}
.btn-quote{position:absolute;left:97px;top:127px;width:87px;height:22px;background:var(--navy-deep);color:var(--white);font-size:7px;font-weight:600;display:flex;align-items:center;justify-content:center;gap:5px}

/* welcome */
.welcome{position:absolute;top:304px;left:0;width:690px;height:120px;text-align:center}
.welcome h2{font-family:"Roboto",sans-serif;font-weight:300;font-size:21px;color:var(--navy);margin-top:20px}
.welcome p{width:495px;margin:9px auto 0;font-size:6.4px;line-height:8.2px;color:var(--body-text)}

/* services */
.services{position:absolute;top:424px;left:0;width:690px;height:314px;background:var(--ice)}
.grid{position:absolute;top:46px;left:88px;width:517px;display:grid;grid-template-columns:repeat(3,172px);grid-auto-rows:110px;gap:1px}
.card{background:var(--white);text-align:center;padding-top:10px}
.card svg{display:block;margin:0 auto;height:28px}
.card h3{font-family:"Roboto",sans-serif;font-weight:400;font-size:8.5px;color:var(--navy-deep);margin-top:6px}
.card .rule{width:38px;height:1px;background:var(--sky);margin:5px auto 6px}
.card p{font-size:6px;line-height:7.5px;color:var(--grey-text);padding:0 26px}
.card.call{background:var(--sky);color:var(--white);padding-top:14px}
.card.call .lbl{font-size:7.5px}
.card.call .num{font-family:"Roboto",sans-serif;font-size:13px;margin-top:7px}
.card.call p{color:var(--white);margin-top:5px}
.card.call .btn{display:inline-block;margin-top:9px;width:83px;height:20px;line-height:20px;background:var(--navy-deep);font-size:6.5px}

/* articles */
.articles{position:absolute;top:770px;left:88px;width:517px;display:grid;grid-template-columns:repeat(3,172px);gap:0 1px}
.article{text-align:center}
.article .photo{height:128px}
.p1{background:linear-gradient(135deg,#e7e7e4,#b8b7b2)}
.p2{background:linear-gradient(135deg,#8b8f98,#c9c2b8 55%,#585a62)}
.p3{background:linear-gradient(135deg,#e9ecef,#c3c9d0)}
.article h4{font-family:"Roboto",sans-serif;font-weight:400;font-size:8.5px;color:var(--navy-deep);margin-top:8px}
.article .rule{width:38px;height:1px;background:var(--sky);margin:5px auto 6px}
.article p{font-size:6px;line-height:7.5px;color:var(--grey-text);padding:0 12px}
.article .more{display:block;margin-top:4px;font-size:6.5px;color:var(--sky)}

/* partners */
.divider{position:absolute;top:997px;left:88px;width:517px;height:1px;background:#dcdfe2}
.partners{position:absolute;top:1014px;left:88px;width:517px;height:26px;display:flex;justify-content:space-between;align-items:center;padding:0 17px}
.partners span{font-family:"Open Sans",sans-serif;font-weight:700;font-size:8px;color:#4a5058}

/* footer */
.footer{position:absolute;top:1051px;left:0;width:690px;height:107px;background:var(--footer)}
.fcol{position:absolute;top:25px;font-size:6.3px;color:var(--navy);line-height:12.8px}
.fcol.c1{left:98px}
.fcol.c2{left:250px;top:26px}
.subscribe{position:absolute;left:351px;top:26px}
.subscribe h5{font-size:6.5px;font-weight:400;color:var(--navy-deep)}
.form{display:flex;gap:10px;margin-top:8px}
.form .field{width:146px;height:20px;background:var(--white);font-size:6px;color:#9aa0a6;padding-left:6px;line-height:20px}
.form .go{width:83px;height:20px;background:var(--sky);color:var(--white);font-size:8px;text-align:center;line-height:20px}
.fsocial{display:flex;gap:5px;margin-top:9px}
.fsocial span{width:13px;height:13px;border-radius:50%;background:var(--navy-deep)}
.copyright{position:absolute;top:1174px;left:0;width:690px;text-align:center;font-size:5.5px;color:#333}
</style>
</head>
<body>

<div class="topbar">
  <a class="contact" href="#">Contact Us</a>
  <div class="socials" aria-label="Social links"><span></span><span></span><span></span><span></span></div>
  <a class="quote-tab" href="#">QUICK QUOTE</a>
</div>

<header class="header">
  <div class="logo">Marcus Delbridge Finance</div>
  <nav class="mainnav">
    <a class="active" href="#">HOME</a>
    <a href="#">ABOUT MARCUS</a>
    <a href="#">CONTACT</a>
  </nav>
  <div class="phone">555-014-8820</div>
</header>

<nav class="servicenav">
  <a href="#">Equipment Finance</a>
  <a href="#">Commercial Finance</a>
  <a href="#">Construction Finance</a>
  <a href="#">Business Finance</a>
  <a href="#">Bridging Finance</a>
</nav>

<section class="hero">
  <div class="hero-photo" role="img" aria-label="Smiling businessman in a dark suit offering a handshake"></div>
  <div class="hero-text">
    <h1>FINANCE SOLUTIONS</h1>
    <p>LOREM IPSUM DOLOR SIT AMET, CONSECTETUR ADIPISCING ELIT. SED EUISMOD ODIO</p>
  </div>
  <a class="btn-quote" href="#">
    <svg width="10" height="5" viewBox="0 0 10 5"><path d="M0 2.5h9M7 .5l2 2-2 2" stroke="#fff" stroke-width=".8" fill="none"/></svg>
    GET QUOTE
  </a>
</section>

<section class="welcome">
  <h2>Welcome</h2>
  <p>Lorem ipsum dolor sit amet, consectetur adipiscing elit. Sed vel semper risus, id consequat mauris. Curabitur sit amet accumsan est, at sollicitudin nunc. Nullam semper at nulla eget dictum. Fusce mollis laoreet mattis. Suspendisse eget sagittis dolor. Phasellus facilisis quam dolor. Donec ac odio et justo ultricies efficitur at pharetra sem. Sed blandit, velit in tristique volutpat, libero mi pellentesque dolor, sed porta eros lacus ut odio. Etiam tempus ipsum justo, eget faucibus augue dignissim ac. Phasellus sit amet vulputate felis. Proin ligula ante, porta id posuere in, finibus sit amet mauris.</p>
</section>

<section class="services">
  <div class="grid">
    <div class="card">
      <svg viewBox="0 0 30 28"><rect x="4" y="4" width="12" height="14" fill="none" stroke="#00a9e8" stroke-width="1.6"/><path d="M20 2v20h8" stroke="#00a9e8" stroke-width="1.6" fill="none"/><circle cx="7" cy="23" r="3.5" fill="#00a9e8"/><circle cx="16" cy="23" r="2.5" fill="#0d3a66"/></svg>
      <h3>Equipment Finance</h3><div class="rule"></div>
      <p>Lorem ipsum dolor sit amet, consectetur adipiscing elit. Sed euismod odio vitae orci tempor, eget egestas nunc condimentum.</p>
    </div>
    <div class="card">
      <svg viewBox="0 0 30 28"><rect x="3" y="18" width="5" height="9" fill="#00a9e8"/><rect x="10" y="14" width="5" height="13" fill="#0d3a66"/><rect x="17" y="16" width="5" height="11" fill="#00a9e8"/><rect x="24" y="10" width="5" height="17" fill="#00a9e8"/><path d="M3 12l8-6 6 4 10-8" stroke="#00a9e8" stroke-width="1.5" fill="none"/></svg>
      <h3>Commercial Finance</h3><div class="rule"></div>
      <p>Lorem ipsum dolor sit amet, consectetur adipiscing elit. Sed euismod odio vitae orci tempor, eget egestas nunc condimentum.</p>
    </div>
    <div class="card">
      <svg viewBox="0 0 30 28"><rect x="7" y="2" width="16" height="25" fill="none" stroke="#00a9e8" stroke-width="1.6"/><rect x="10" y="6" width="3" height="3" fill="#00a9e8"/><rect x="17" y="6" width="3" height="3" fill="#00a9e8"/><rect x="10" y="12" width="3" height="3" fill="#00a9e8"/><rect x="17" y="12" width="3" height="3" fill="#00a9e8"/><rect x="13" y="20" width="4" height="7" fill="#0d3a66"/></svg>
      <h3>Construction Finance</h3><div class="rule"></div>
      <p>Lorem ipsum dolor sit amet, consectetur adipiscing elit. Sed euismod odio vitae orci tempor, eget egestas nunc condimentum.</p>
    </div>
    <div class="card">
      <svg viewBox="0 0 30 28"><path d="M2 10l8-4 6 3 6-3 6 4-6 10-6 4-8-6z" fill="#00a9e8"/><path d="M10 14l5 4" stroke="#fff" stroke-width="1"/></svg>
      <h3>Business Finance</h3><div class="rule"></div>
      <p>Lorem ipsum dolor sit amet, consectetur adipiscing elit. Sed euismod odio vitae orci tempor, eget egestas nunc condimentum.</p>
    </div>
    <div class="card">
      <svg viewBox="0 0 30 28"><rect x="3" y="5" width="18" height="16" fill="none" stroke="#00a9e8" stroke-width="1.6"/><rect x="3" y="5" width="18" height="4" fill="#0d3a66"/><rect x="14" y="17" width="14" height="9" fill="#fff" stroke="#00a9e8" stroke-width="1.4"/><circle cx="21" cy="21.5" r="2" fill="none" stroke="#00a9e8"/></svg>
      <h3>Bridging Finance</h3><div class="rule"></div>
      <p>Lorem ipsum dolor sit amet, consectetur adipiscing elit. Sed euismod odio vitae orci tempor, eget egestas nunc condimentum.</p>
    </div>
    <div class="card call">
      <div class="lbl">For More Info Call:</div>
      <div class="num">555-014-8820</div>
      <p>Lorem ipsum dolor sit amet, consectetur adipiscing elit.</p>
      <a class="btn" href="#">QUICK QUOTE</a>
    </div>
  </div>
</section>

<section class="articles">
  <article class="article">
    <div class="photo p1" role="img" aria-label="Person in a hoodie working on a laptop"></div>
    <h4>In aliquam tortor et nunc maximus</h4><div class="rule"></div>
    <p>Lorem ipsum dolor sit amet, consectetur adipiscing elit. Sed euismod odio vitae orci tempor, eget egestas nunc condimentum.</p>
    <a class="more" href="#">- Read more</a>
  </article>
  <article class="article">
    <div class="photo p2" role="img" aria-label="Colleagues reviewing charts on a laptop at a desk"></div>
    <h4>In aliquam tortor et nunc maximus</h4><div class="rule"></div>
    <p>Lorem ipsum dolor sit amet, consectetur adipiscing elit. Sed euismod odio vitae orci tempor, eget egestas nunc condimentum.</p>
    <a class="more" href="#">- Read more</a>
  </article>
  <article class="article">
    <div class="photo p3" role="img" aria-label="Customer support team with headsets in an office"></div>
    <h4>In aliquam tortor et nunc maximus</h4><div class="rule"></div>
    <p>Lorem ipsum dolor sit amet, consectetur adipiscing elit. Sed euismod odio vitae orci tempor, eget egestas nunc condimentum.</p>
    <a class="more" href="#">- Read more</a>
  </article>
</section>

<div class="divider"></div>
<div class="partners" aria-label="Lending partners">
  <span>Harlow Bank</span><span>Ridgeway Bank</span><span>Coralline</span><span>Brenmoor</span><span>Tessel Capital</span><span>Quillon</span><span>Venwick</span>
</div>

<footer class="footer">
  <div class="fcol c1">
    <div>EQUIPMENT FINANCE</div><div>COMMERCIAL FINANCE</div><div>CONSTRUCTION FINANCE</div><div>BUSINESS FINANCE</div><div>BRIDGING FINANCE</div>
  </div>
  <div class="fcol c2">
    <div>HOME</div><div>ABOUT MARCUS</div><div>CONTACT</div>
  </div>
  <div class="subscribe">
    <h5>SUBSCRIBE FOR THE LATEST NEWS</h5>
    <div class="form"><div class="field">Enter Your Email</div><div class="go">SUBSCRIBE</div></div>
    <div class="fsocial"><span></span><span></span><span></span><span></span></div>
  </div>
</footer>
<div class="copyright">Copyright 2017 delbridgefinance.com All Rights Reserved.</div>

</body>
</html>
```